High-End Print/Digital Ad for Unique Luxury Travel Company Required

Objective:
Design a compelling and visually striking advertisement that highlights our company’s unmatched luxury travel experiences. The ad should elevate our brand image, spark curiosity, and drive prospective clients to contact us.
Target Audience:
• Affluent individuals seeking extraordinary, tailor-made travel experiences
• Affluent, luxury, high-net-worth individuals looking for value, expertise, and white-glove service
• Professionals or retirees who appreciate unique, thoughtfully curated travel over mainstream tourism
Key Messages to Communicate:
• One-of-a-kind luxury travel: Once-in-a-lifetime experiences that are curated with creativity and meticulous attention to detail
• Exceptional service: White-glove, personalized planning from start to finish
• 38 years’ travel experience – expert knowledge of destinations, modes of travel, premium accommodations and well-established, meaningful industry connections.
• Highly trusted: Cruise line executives often say, “No one does what you do.”
Tone and Style:
• Elegant, luxurious, sophisticated
• Eye-catching, polished, and modern
• Professional but warm—conveys trust and credibility
• High-impact visuals (full-bleed imagery, custom graphics, or high-end photography)
Deliverables:
• One full-page print ad and digital ad
• Ready-to-print, high-resolution file + working file (PSD, AI, etc.)
Optional: Social media-optimized version or short motion-graphic variation (if designer offers it)
Inspiration & Visual Style Suggestions:
• Think Lumen Voyages, Harrow Pike Wanderer, Silver Quill, or Orvel Retreats ad styles
• Large, emotive imagery with elegant typography
• Clean layout that speaks luxury, clarity, and trust
Copy Direction (draft):
For those who’ve explored the world—and crave something beyond the ordinary.
Each journey is a masterfully curated experience, rich in detail, seamless in execution, and unforgettable in every way.
Founded in 1997, Tidewell Journeys is a unique travel company specializing in cruising, all-inclusive luxury properties, and tours world-wide for individuals, groups, and incentives.
We offer an exceptional range of services designed to ensure every journey is flawlessly executed and truly unforgettable.
Let us help you plan your next extraordinary adventure.
Note: You may refine the copy slightly based on layout or format needs.
Other Resources for References:
1. Website - www.tidewelljourneys-example.com

```html
<!DOCTYPE html>
<html lang="en">
<head>
<meta charset="utf-8">
<title>Tidewell Journeys — Once-in-a-Lifetime Experience</title>
<link rel="stylesheet" href="https://fonts.googleapis.com/css2?family=EB+Garamond:ital,wght@0,400;0,600;0,700;1,400&display=swap">
<style>
  :root {
    --backdrop: #959595;
    --paper: #ffffff;
    --ink: #231f20;
    --navy: #1f4a86;
    --dots: #a7a7a7;
    --sky-warm: #e9b56a;
    --sky-cool: #4f86c4;
    --city: #c98a55;
    --garden: #6b8a3e;
    --mosaic: #e6c646;
    --storm: #36508f;
    --sea: #2c3f66;
  }
  * { margin: 0; padding: 0; box-sizing: border-box; }
  html, body { width: 885px; height: 1200px; overflow: hidden; }
  body {
    position: relative;
    background: var(--backdrop);
    font-family: "EB Garamond", Georgia, serif;
    color: var(--ink);
  }
  .page {
    position: absolute;
    left: 50px; top: 46px;
    width: 786px; height: 1108px;
    background: var(--paper);
  }
  .headline { position: absolute; left: 0; width: 100%; text-align: center; font-weight: 700; text-transform: uppercase; line-height: 1; }
  .headline--kicker { top: 62px; font-size: 25px; letter-spacing: 0.2px; }
  .headline--main { top: 100px; font-size: 37px; letter-spacing: 0.3px; }
  .headline--close { top: 154px; font-size: 25px; }

  .dots-h { position: absolute; height: 0; border-top: 2.5px dotted var(--dots); }
  .dots-v { position: absolute; width: 0; border-left: 2.5px dotted var(--dots); }

  .seal {
    position: absolute; left: 375px; top: 201px;
    width: 36px; height: 36px; border-radius: 50%;
    background: var(--navy);
  }

  .hero {
    position: absolute; left: 72px; top: 263px;
    width: 644px; height: 360px;
    background:
      linear-gradient(180deg, transparent 72%, var(--mosaic) 92%),
      linear-gradient(180deg, var(--sky-warm) 0%, #f1cf8f 18%, var(--city) 40%, #b58d78 60%, var(--garden) 78%),
      linear-gradient(90deg, #e49a4e, var(--sky-cool));
    background-blend-mode: normal, multiply, normal;
  }
  .caption { position: absolute; left: 0; width: 100%; top: 627px; text-align: center; font-size: 13.5px; }

  .col-intro { position: absolute; left: 72px; top: 674px; width: 210px; font-size: 11.6px; line-height: 15.8px; }
  .col-intro p + p { margin-top: 15.5px; }

  .ship-frame {
    position: absolute; left: 301px; top: 680px;
    width: 189px; height: 241px;
    background: #ededed;
    box-shadow: 0 14px 14px -10px rgba(0,0,0,0.45);
  }
  .ship-photo {
    position: absolute; left: 6px; top: 6px;
    width: 177px; height: 229px;
    background: linear-gradient(180deg, var(--storm) 0%, #6d7fae 50%, #d8b98a 62%, var(--sea) 78%, #1d2a45 100%);
  }

  .col-points { position: absolute; left: 522px; top: 676px; width: 200px; font-size: 11.6px; line-height: 14.2px; }
  .point + .point { margin-top: 10px; }
  .point h3 { color: var(--navy); font-weight: 700; font-size: 12.2px; line-height: 15px; }
  .point em { font-style: italic; }

  .invite { position: absolute; left: 0; width: 100%; top: 955px; text-align: center; font-size: 13.5px; }

  .brand {
    position: absolute; left: 0; width: 100%; top: 1008px;
    display: flex; justify-content: center; align-items: center; gap: 10px;
  }
  .brand__mark { width: 26px; height: 26px; border-radius: 50%; background: var(--navy); }
  .brand__name { color: var(--navy); font-size: 25px; font-weight: 400; letter-spacing: 0.5px; text-transform: uppercase; line-height: 1; }

  .contact { position: absolute; left: 0; width: 100%; top: 1045px; text-align: center; font-size: 12.4px; white-space: nowrap; }
  .contact b { font-weight: 700; }
  .contact .sep { color: var(--dots); margin: 0 4px; }
</style>
</head>
<body>
  <main class="page">
    <h1 class="headline headline--kicker">Four Decades of Inspiration</h1>
    <h2 class="headline headline--main">Once-in-a-Life Time Experience</h2>
    <h2 class="headline headline--close">Comes Your Way</h2>

    <div class="dots-h" style="left:171px; top:219px; width:196px;"></div>
    <div class="seal"></div>
    <div class="dots-h" style="left:419px; top:219px; width:196px;"></div>

    <div class="hero" role="img" aria-label="Sunset view over a colourful city from a mosaic-tiled park terrace with gingerbread-style pavilions and palm trees"></div>
    <p class="caption">Imagine what we could do if we shared our ideas</p>
    <div class="dots-h" style="left:194px; top:650px; width:399px;"></div>

    <section class="col-intro">
      <p>For those who’ve explored the world and crave something beyond the ordinary.</p>
      <p>Each journey is a masterfully curated experience, rich in detail, seamless in execution, and unforgettable in every way.</p>
      <p>Founded in 1997, Tidewell Journeys is a unique travel company specializing in cruising, all-inclusive luxury properties, and tours world-wide for individuals, groups, and incentives.</p>
      <p>We offer an exceptional range of services designed to ensure every journey is flawlessly executed and truly unforgettable.</p>
    </section>

    <div class="dots-v" style="left:287px; top:681px; height:243px;"></div>

    <figure class="ship-frame">
      <div class="ship-photo" role="img" aria-label="Large cruise ship at sea under a dramatic cloudy blue sky at dusk"></div>
    </figure>

    <div class="dots-v" style="left:502px; top:681px; height:243px;"></div>

    <section class="col-points">
      <div class="point">
        <h3>One-of-a-kind luxury travel</h3>
        <p>Once-in-a-lifetime experiences that are curated with creativity and meticulous attention to detail</p>
      </div>
      <div class="point">
        <h3>Exceptional service</h3>
        <p>White-glove, personalized planning from start to finish</p>
      </div>
      <div class="point">
        <h3>38 years’ travel experience</h3>
        <p>Expert knowledge of destinations, modes of travel, premium accommodations and well-established, meaningful industry connections.</p>
      </div>
      <div class="point">
        <h3>Highly trusted</h3>
        <p>Cruise line executives often say, <em>“No one does what you do.”</em></p>
      </div>
    </section>

    <p class="invite">Let us help you plan your next extraordinary adventure.</p>
    <div class="dots-h" style="left:301px; top:983px; width:184px;"></div>

    <div class="brand">
      <span class="brand__mark"></span>
      <span class="brand__name">Tidewell Journeys</span>
    </div>

    <p class="contact">toll-free 877.555.0142<span class="sep">|</span><b>p</b> 816.555.0187<span class="sep">|</span><b>e</b> travelplans@tidewelljourneys-example.com<span class="sep">|</span>tidewelljourneys-example.com</p>
  </main>
</body>
</html>
```